Tech company needs a brochure design

Hi there.

We have written the text for a 4 page brochure, and this needs laying out.

We are in the process of rebranding, and have a new logo, but haven't yet established a colour pallete or design style.

Our current preference is for simple and bold. An example is the current website holding page is marvaxen.io

Colour pallet should pull from the logo for primary colours, but we're open to secondary colours.

The layout in the document is not set in stone, but should be used as a guideline.

The final text is almost ready (we're polishing the phrasing), but it will be almost identical in the number of words and layout.

Target Market(s)

Typically, they are companies that operate in highly regulated industries, such as Financial Services, Telecoms or Healthcare, are data-centric and need to adhere to regulations such as GDPR. Or, data-sensitive, such as Legal, Accountancy or even Retail, where a breach of the network would give access to highly sensitive information.

Regulations and compliance requirements affect the systems they have in place, particularly when it comes to managing and securing data.

All of this impacts the IT infrastructure that is needed, and Marvaxen can provide a seamless network that allows for all the regulations and doesn’t affect the working environment.

Marvaxen sells into these environments at a senior level – IT Director, CIO, CTO.

Industry/Entity Type

Cyber Security

Font styles to use
Sans Serif
Other font styles liked:
• Nexa

Requirements
Must have
• 4 pages in landscape
Clean design
Be appropriate for corporate/business environments but still have vitality
use attached logo for colours - Gray is #2f2f2f
Nice to have
• Can be white or dark based
Should not have
• Not Fussy
Icons that don’t have any relevance

```html
<!DOCTYPE html>
<html lang="en">
<head>
<meta charset="utf-8">
<title>Marvaxen Brochure</title>
<link rel="stylesheet" href="https://fonts.googleapis.com/css2?family=Montserrat:wght@300;400;500;600;700;800&display=swap">
<style>
:root{
  --bg:#e2e2e2;
  --paper:#f7f7f7;
  --paper-shade:#e6e6e6;
  --ink:#2f2f2f;
  --ink-soft:#6b6b6b;
  --red:#c8202a;
  --orange:#e8651e;
  --panel:#ebebeb;
}
*{box-sizing:border-box;margin:0;padding:0}
html,body{width:1200px;height:2361px;overflow:hidden}
body{background:var(--bg);font-family:"Montserrat",sans-serif;color:var(--ink);position:relative}
.page{position:absolute;background:linear-gradient(135deg,var(--paper) 0%,var(--paper) 40%,var(--paper-shade) 100%);box-shadow:0 18px 40px rgba(0,0,0,.12);overflow:hidden}

/* cover */
.cover{left:150px;top:150px;width:900px;height:636px}
.brand{position:absolute;display:flex;align-items:center;gap:8px;font-weight:700;color:var(--ink)}
.cover .brand{left:70px;top:70px;font-size:40px}
.brand .dot{width:12px;height:12px;border-radius:50%;background:var(--orange)}
.flight-art{position:absolute;border-radius:6px;background:
  radial-gradient(circle at 82% 18%,rgba(232,101,30,.35) 0,rgba(232,101,30,0) 22%),
  linear-gradient(160deg,#f2f2f2 0%,#e7e7e7 60%,#dedede 100%)}
.cover .flight-art{left:250px;top:150px;width:300px;height:486px;border-radius:6px 6px 0 0}
.cover-copy{position:absolute;right:60px;bottom:80px;text-align:right;line-height:1.25}
.cover-copy .sub{font-weight:300;font-size:22px;color:var(--ink)}
.cover-copy .bold{font-weight:800;font-size:22px;text-transform:uppercase;margin-top:10px}
.cover-copy .bold + .bold{margin-top:0}
.cover-copy .reward{font-weight:800;font-size:32px;color:var(--orange);text-transform:uppercase}

/* spread */
.inner-left{left:40px;top:936px;width:560px;height:396px;padding:26px 30px}
.inner-right{left:600px;top:936px;width:560px;height:396px;padding:34px 30px;background:linear-gradient(225deg,var(--paper) 0%,var(--paper) 45%,var(--paper-shade) 100%)}
.inner-left::after{content:"";position:absolute;right:0;top:0;width:30px;height:100%;background:linear-gradient(90deg,rgba(0,0,0,0),rgba(0,0,0,.06))}
.title{font-weight:600;font-size:15px;line-height:1.2;border-left:3px solid var(--red);padding-left:8px}
.small{font-size:7.2px;line-height:1.55;color:var(--ink-soft);margin-top:6px}
.small em{font-style:italic}
.stats{position:absolute;left:30px;right:30px;bottom:26px;height:120px;background:var(--panel);border-radius:10px;display:flex;justify-content:space-around;align-items:center}
.stat{text-align:center;width:140px}
.stat .icon{width:28px;height:28px;border-radius:50%;border:1.5px solid var(--ink-soft);margin:0 auto 8px}
.stat .num{font-weight:800;font-size:30px;background:linear-gradient(90deg,var(--red),var(--orange));-webkit-background-clip:text;background-clip:text;color:transparent}
.stat .cap{font-size:8px;color:var(--ink-soft);line-height:1.3}
.sub-title{font-weight:600;font-size:9px;color:var(--ink);border-left:2px solid var(--red);padding-left:6px}
.box{background:var(--panel);border-radius:8px;padding:9px 11px;margin-top:10px;width:290px}
.box .sub-title{font-size:10px;font-weight:500}
.inner-right .flight-art{right:24px;top:110px;width:190px;height:266px}

/* back cover */
.back{left:150px;top:1482px;width:900px;height:636px;padding:56px 60px;background:linear-gradient(135deg,#fafafa,#ececec)}
.back .title{font-size:14px;font-weight:600;text-transform:uppercase}
.back .small{font-size:9px;margin-bottom:18px}
.ways{background:var(--panel);border-radius:10px;padding:16px 20px;margin-bottom:18px}
.ways h3{font-weight:400;font-size:15px;margin-bottom:10px}
.ways-cols{display:flex;gap:26px}
.ways-cols div{flex:1;font-size:8.6px;line-height:1.5;color:var(--ink-soft)}
.ways-cols b{color:var(--ink);font-weight:700}
.ways-cols b span{color:var(--orange)}
.peace{font-weight:800;font-size:13px;text-transform:uppercase}
.contact-bar{position:absolute;left:60px;right:60px;bottom:40px;height:82px;display:flex}
.cta{width:260px;background:var(--ink);color:#fff;font-size:13px;line-height:1.3;padding:16px 20px;border-radius:8px 0 0 8px;clip-path:polygon(0 0,92% 0,100% 50%,92% 100%,0 100%)}
.details{flex:1;margin-left:-8px;background:linear-gradient(90deg,var(--red),var(--orange));color:#fff;padding:16px 30px;border-radius:0 10px 10px 0;clip-path:polygon(0 0,100% 0,100% 100%,0 100%,4% 50%)}
.details .name{font-weight:600;font-size:14px}
.details p{font-size:9px;margin-top:4px}
</style>
</head>
<body>

<section class="page cover">
  <div class="brand"><span>Marvaxen</span><span class="dot"></span></div>
  <div class="flight-art" role="img" aria-label="Flock of white paper planes with a red paper plane flying ahead along a dashed flight path"></div>
  <div class="cover-copy">
    <p class="sub">Propelling clients<br>through the journey to efficiency</p>
    <p class="bold">Change your thinking</p>
    <p class="bold">Change your approach</p>
    <p class="reward">Reap the rewards</p>
  </div>
</section>

<section class="page inner-left">
  <h2 class="title">A Different Provider<br>A Different Type of Business Solution</h2>
  <p class="small"><em>We are Marvaxen. We have been propelling companies on the journey to automation and efficiency since 2009.</em></p>
  <p class="small">Our expertise lies in modernising, automating and securing complex technical environments. By balancing the requirements of compliance with the realities of technology, process and people, we establish a clean, compliant and secure business setting for our clients, one that is robust, easy to maintain and effortless to adapt and scale.</p>
  <p class="small">We are different from others in our approach. In listening to our clients and applying our unique methodology, we can take stock of the environment and challenge the existing way of doing things, streamlining people, processes and technology in a coordinated fashion to deliver comprehensive and secure solutions that propel our clients forward.</p>
  <p class="small">In providing our clients with an efficient, secure and compliant environment, productivity improves, costs and risk are reduced, and services are delivered in a streamlined manner to establish competitive advantage in the market.</p>
  <div class="stats">
    <div class="stat"><div class="icon"></div><div class="num">84%</div><div class="cap">More efficient IT<br>operations</div></div>
    <div class="stat"><div class="icon"></div><div class="num">92%</div><div class="cap">Increase in speed of<br>execution &amp; delivery</div></div>
    <div class="stat"><div class="icon"></div><div class="num">60%</div><div class="cap">Reduction in costs<br>to the business</div></div>
  </div>
</section>

<section class="page inner-right">
  <h3 class="sub-title">The Changing Landscape</h3>
  <p class="small" style="width:310px">Today's fast-paced business environment is a complex world. Technology and the way that people consume information is evolving at speed and continuously changing. Most organisations have evolved over time and often consist of legacy technologies, added incrementally, making them hard to adapt and time-consuming to manage.</p>
  <p class="small" style="width:310px">These are the environments where Marvaxen excels. We streamline and automate the IT estate, rationalising and securing technology, processes and systems.</p>
  <div class="box">
    <h4 class="sub-title">Digital Efficiency</h4>
    <p class="small">An efficient digital environment will establish competitive advantage in this interconnected world. Marvaxen experts unify and refine this environment with a proven methodology.</p>
  </div>
  <div class="box">
    <h4 class="sub-title">Governance, Risk &amp; Compliance</h4>
    <p class="small">Data is often the lifeblood of companies and regulations abound. Making sense of this and protecting sensitive information is fundamental to your risk profile.</p>
  </div>
  <div class="flight-art" role="img" aria-label="Pyramid of white paper planes led by a red paper plane"></div>
</section>

<section class="page back">
  <h2 class="title">Structuring your business in the right way</h2>
  <p class="small">Budgets are tight, technology and security teams need to do more with less, whilst the business requires an ever-increasing array of new technologies to stay ahead of the competition. Marvaxen provides a holistic wrapper around people, processes and technology to create a more efficient organisation that operates and runs more effectively, enabling you to deliver products and services to market faster while enhancing the customer experience.</p>
  <h2 class="title">Propelling your technology journey</h2>
  <p class="small">Every organisation is different. Requirements differ, structures contrast and objectives vary. One size does not fit all and an all-encompassing view is essential to start the journey from the correct point and achieve the desired outcome. At Marvaxen, we consider our client's entire eco-system, redefining the problem to build the solution that will drive your business forward.</p>
  <div class="ways">
    <h3>There are several ways we work with our clients.</h3>
    <div class="ways-cols">
      <div><b>Manage the journey <span>For You</span></b><br>Marvaxen takes control and full responsibility, so you don't have to worry. We manage the risk. You gain the results and the desired outcome.</div>
      <div><b>Go on the journey <span>With You</span></b><br>We work in partnership with you, enhancing your existing team and upskilling your capabilities along the way.</div>
      <div><b>The journey is taken <span>By You</span></b><br>Marvaxen provides you with the right tools to make the journey yourself.</div>
    </div>
  </div>
  <h2 class="peace">Your peace of mind is essential</h2>
  <p class="small">Building trust and working in partnership with our clients is important to us. Marvaxen follows a framework-led, principle-based approach, with a unique methodology, and has extensive technical expertise across the leading technologies in the market.</p>
  <div class="contact-bar">
    <div class="cta">Contact us today to talk about setting your business on the journey to efficiency</div>
    <div class="details">
      <div class="name">Marvaxen</div>
      <p>E: info@marvaxen.io &nbsp;|&nbsp; W: marvaxen.io &nbsp;|&nbsp; T: +44 (0)1632 960418</p>
      <p>Unit 7 | Elm Court | Station Road | Ashbury | Westshire | AB1 2CD</p>
    </div>
  </div>
</section>

</body>
</html>
```